We’re a real estate firm that has landed a big builder in a neighboring state. Our branding needs...

We are a real estate firm who represents various builders along with doing resale here in Oregon. Our firm is growing to represent a big builder in Washington State and we’ll have another 40 brokers on our team. We need rebranding. As in, a new logo ( the house logo we have now looks cartoonish, hate it). We need new cards, something to really stand out. I’ve been thinking of using those NFC cards from ZEP or the ones with the seam color. I likely want two or three designs, a darker (as in a background color of black or grey) , a light one ( again I mean background color) and a credit card style (either plastic w an embossed name/number on front, or metal ). I’m thinking dark background for cc, or silver if it’s metal. That’s my thoughts, but you are the artists, so maybe you have an idea I haven’t considered. Our colors were black and red, but we don’t have to stick to that. Just nothing too busy. Oh, and we are typically representing the local, higher quality builders in our area (just below custom), but not national. Subdivisions are near the Kell Varney, Brisco, and Thornfield Crest sites. We are super excited, but without a lot of time to change the “look” of our brokerage. So I’ll be deciding and moving forward within 24 hours tops. Our name is Real Estate Summit Alliance ( we cant change the name because of timeline and business license) Thank you!

Industry/Entity Type

Real Estate

Contact Information for Business Card

The usual. Name of firm. Name of cardholder. Contact info.

Font styles to use
Serif
Sans Serif

Colors

Designer to choose colors to be used in the design.

Requirements
Must have
• A sleek or simple look. I included photos of cards with stylistic attributes we like. Thank you
Nice to have
• We really like the black backgrounds. With foil or embossed detail. We also like the black on black. Matte black card with raised shiny black detail. But still eye catching.
Should not have
• No ornate or busy looking style. We don’t want anything cluttered.

```html
<!DOCTYPE html>
<html lang="en">
<head>
<meta charset="utf-8">
<title>Real Estate Summit Alliance — Business Card</title>
<link href="https://fonts.googleapis.com/css2?family=Work+Sans:wght@400;500;600&display=swap" rel="stylesheet">
<style>
  :root {
    --stage: #1b1b1b;
    --card: #242424;
    --card-edge: #2c2c2c;
    --ink: #f4f4f4;
    --ink-soft: #e6e6e6;
    --accent: #d3202a;
  }
  * { box-sizing: border-box; margin: 0; padding: 0; }
  html, body {
    width: 1200px; height: 900px; overflow: hidden;
    background: var(--stage);
    font-family: "Work Sans", Arial, sans-serif;
    color: var(--ink);
  }
  .canvas {
    position: relative; width: 1200px; height: 900px;
  }
  .card {
    position: absolute; left: 250px; width: 700px; height: 400px;
    background: linear-gradient(135deg, var(--card) 0%, var(--card-edge) 100%);
    border-bottom: 6px solid var(--accent);
    box-shadow: 0 12px 30px rgba(0,0,0,.55);
  }
  .card--front { top: 30px; }
  .card--back { top: 470px; }

  .wordmark {
    display: flex; align-items: center; gap: 14px;
    font-weight: 600; color: var(--ink); line-height: 1.15;
  }
  .wordmark__square {
    width: 18px; height: 18px; background: var(--accent); flex: none;
  }
  .card--front .wordmark {
    position: absolute; left: 50%; top: 50%;
    transform: translate(-50%, -50%);
    font-size: 34px;
  }
  .card--back .wordmark {
    position: absolute; left: 48px; top: 150px;
    font-size: 25px;
  }

  .divider {
    position: absolute; left: 345px; top: 70px;
    width: 2px; height: 240px; background: var(--ink-soft);
  }

  .details {
    position: absolute; left: 380px; top: 72px; width: 300px;
  }
  .details__name {
    color: var(--accent); font-weight: 500;
    font-size: 27px; letter-spacing: 2px; text-transform: uppercase;
  }
  .details__role {
    font-size: 15px; letter-spacing: .5px; margin-top: 2px;
  }
  .details__address {
    font-size: 15px; line-height: 1.55; letter-spacing: .5px;
    margin-top: 20px; font-style: normal;
  }
  .contact {
    list-style: none; margin-top: 14px;
    font-size: 15px; letter-spacing: .5px;
  }
  .contact li {
    display: flex; align-items: center; gap: 10px; line-height: 1.6;
  }
  .contact svg { width: 12px; height: 12px; flex: none; }
</style>
</head>
<body>
<main class="canvas">

  <section class="card card--front" aria-label="Card front">
    <div class="wordmark">
      <span class="wordmark__square"></span>
      <span>Real Estate<br>Summit Alliance</span>
    </div>
  </section>

  <section class="card card--back" aria-label="Card back">
    <div class="wordmark">
      <span class="wordmark__square"></span>
      <span>Real Estate<br>Summit Alliance</span>
    </div>

    <div class="divider"></div>

    <div class="details">
      <h1 class="details__name">Daniel Mercer</h1>
      <p class="details__role">Director</p>
      <address class="details__address">
        4120 SE Ridgeline Ave.<br>
        Suite 305-B,<br>
        Milwaukie, OR 97222
      </address>
      <ul class="contact">
        <li>
          <svg viewBox="0 0 12 12" aria-hidden="true"><path d="M3 1 L5 3.5 L4 5 Q5.5 7.5 7 8 L8.5 7 L11 9 L9.5 11 Q4 10 1 3 Z" fill="var(--accent)"/></svg>
          (503) 555-0142
        </li>
        <li>
          <svg viewBox="0 0 12 12" aria-hidden="true"><rect x="1" y="2.5" width="10" height="7" fill="none" stroke="var(--accent)" stroke-width="1.3"/><path d="M1 2.5 L6 6.5 L11 2.5" fill="none" stroke="var(--accent)" stroke-width="1.3"/></svg>
          dmercer.summit@mail.com
        </li>
        <li>
          <svg viewBox="0 0 12 12" aria-hidden="true"><circle cx="6" cy="6" r="5" fill="none" stroke="var(--accent)" stroke-width="1.2"/><ellipse cx="6" cy="6" rx="2.2" ry="5" fill="none" stroke="var(--accent)" stroke-width="1"/><path d="M1 6 H11" stroke="var(--accent)" stroke-width="1"/></svg>
          www.summitalliancehomes.com
        </li>
      </ul>
    </div>
  </section>

</main>
</body>
</html>
```